The Plate Compass

Cutting Through the Noise to What Actually Works.

Nutrition book

Target Market(s)

People looking to be or get healthy and eat right.

```html
<!DOCTYPE html>
<html lang="en">
<head>
<meta charset="UTF-8">
<title>The Plate Compass – Book Cover</title>
<link rel="stylesheet" href="https://fonts.googleapis.com/css2?family=Poppins:wght@500;600;700;800&display=swap">
<style>
  :root {
    --stage: #ffffff;
    --paper-light: #f1e9d7;
    --paper-mid: #e9dfc8;
    --paper-edge: #ddd0b4;
    --ink-dark: #15301f;
    --ink-green: #4c6b2a;
    --ink-sub: #1d3a2a;
    --label-ink: #3a2616;
    --rule: #8d8a6a;
    --leader: #8a4b3a;
    --leaf: #4f8f2f;
  }
  html, body {
    margin: 0;
    padding: 0;
    width: 1200px;
    height: 2662px;
    overflow: hidden;
    background: var(--stage);
  }
  .canvas {
    position: relative;
    width: 1200px;
    height: 2662px;
  }
  .cover {
    position: absolute;
    left: 100px;
    top: 580px;
    width: 1000px;
    height: 1502px;
    background:
      radial-gradient(ellipse at 50% 45%, var(--paper-light) 0%, var(--paper-mid) 60%, var(--paper-edge) 100%);
    font-family: "Poppins", sans-serif;
    overflow: hidden;
  }
  .title-kicker {
    position: absolute;
    top: 50px;
    left: 0;
    width: 100%;
    display: flex;
    align-items: center;
    justify-content: center;
    gap: 22px;
    font-weight: 800;
    font-size: 80px;
    line-height: 1;
    color: var(--ink-dark);
  }
  .title-kicker .dash {
    width: 95px;
    height: 3px;
    background: var(--ink-green);
  }
  .title-main,
  .title-accent {
    position: absolute;
    left: 0;
    width: 100%;
    text-align: center;
    font-weight: 800;
    line-height: 1;
    letter-spacing: -1px;
  }
  .title-main {
    top: 128px;
    font-size: 128px;
    color: var(--ink-dark);
  }
  .title-accent {
    top: 238px;
    font-size: 128px;
    color: var(--ink-green);
  }
  .title-rule {
    position: absolute;
    top: 380px;
    left: 118px;
    width: 762px;
    height: 2px;
    background: var(--rule);
  }
  .subtitle {
    position: absolute;
    top: 402px;
    left: 0;
    width: 100%;
    text-align: center;
    font-weight: 500;
    font-size: 43px;
    line-height: 52px;
    color: var(--ink-sub);
  }
  .hierarchy {
    position: absolute;
    left: 0;
    top: 560px;
    width: 1000px;
    height: 700px;
  }
  .tier-label {
    position: absolute;
    font-weight: 600;
    font-size: 31px;
    line-height: 1;
    color: var(--label-ink);
    white-space: nowrap;
  }
  .tier-label.noise { left: 240px; top: 636px; }
  .tier-label.supplements { left: 650px; top: 712px; }
  .tier-label.meal-timing { left: 113px; top: 800px; }
  .tier-label.food-quality { left: 731px; top: 932px; }
  .tier-label.protein { left: 61px; top: 1016px; }
  .tier-label.calories { left: 799px; top: 1107px; }
  .author-divider {
    position: absolute;
    top: 1280px;
    left: 0;
    width: 1000px;
    height: 60px;
  }
  .author {
    position: absolute;
    top: 1355px;
    left: 0;
    width: 100%;
    text-align: center;
    font-weight: 600;
    font-size: 74px;
    line-height: 1;
    color: var(--ink-dark);
    word-spacing: 14px;
  }
</style>
</head>
<body>
<div class="canvas">
  <div class="cover">
    <div class="title-kicker"><span class="dash"></span>THE<span class="dash"></span></div>
    <div class="title-main">PLATE</div>
    <div class="title-accent">COMPASS</div>
    <div class="title-rule"></div>
    <div class="subtitle">Cutting Through the Noise<br>to What Actually Works</div>

    <svg class="hierarchy" viewBox="0 560 1000 700" xmlns="http://www.w3.org/2000/svg">
      <defs>
        <linearGradient id="foodTones" x1="0" y1="0" x2="0" y2="1">
          <stop offset="0" stop-color="#b8705a"/>
          <stop offset="0.35" stop-color="#6f8249"/>
          <stop offset="0.7" stop-color="#8a7048"/>
          <stop offset="1" stop-color="#8f6e45"/>
        </linearGradient>
      </defs>
      <path role="img"
            aria-label="Food pyramid illustration: diet-plan cards at the tip, then supplements, a clock, vegetables and fruit, meat, fish and eggs, with grains, nuts and cheese at the base on a wooden board"
            d="M478 605 L812 1190 Q895 1195 895 1205 Q880 1218 480 1218 Q80 1218 64 1205 Q64 1195 145 1190 Z"
            fill="url(#foodTones)"/>
      <g fill="none" stroke="var(--leader)" stroke-width="2" stroke-dasharray="3 4">
        <path d="M278 683 L292 698 L405 698"/>
        <path d="M752 756 L740 772 L660 772"/>
        <path d="M160 842 L178 858 L305 858"/>
        <path d="M782 962 L768 948 L690 948"/>
        <path d="M92 1052 L108 1072 L165 1072"/>
        <path d="M862 1142 L850 1160 L800 1160"/>
      </g>
    </svg>
    <div class="tier-label noise">Noise</div>
    <div class="tier-label supplements">Supplements</div>
    <div class="tier-label meal-timing">Meal timing</div>
    <div class="tier-label food-quality">Food quality</div>
    <div class="tier-label protein">Protein</div>
    <div class="tier-label calories">Calories</div>

    <svg class="author-divider" viewBox="0 1280 1000 60" xmlns="http://www.w3.org/2000/svg">
      <line x1="132" y1="1320" x2="452" y2="1320" stroke="var(--rule)" stroke-width="2"/>
      <line x1="543" y1="1320" x2="862" y2="1320" stroke="var(--rule)" stroke-width="2"/>
      <path d="M498 1326 C470 1314 468 1292 478 1284 C496 1290 508 1308 498 1326 Z" fill="var(--leaf)"/>
      <path d="M500 1326 C520 1306 540 1296 552 1298 C548 1318 528 1330 500 1326 Z" fill="var(--leaf)"/>
    </svg>
    <div class="author">Daniel Hartley</div>
  </div>
</div>
</body>
</html>
```